Manufacturer's Representative Group needs a clean new Website

We represent and sell a number of suppliers that design and build products used in Biopharmaceutical manufacturing. Our sales region is in the central US. Our customer base is scientific / engineering based - so clean, we organized design with a focus on the products - easy and clear navigation is necessary. We do not sell direct or warehouse product - so e-commerce is not needed. Our customers will use the website for reference on what we do and offer - we will use the site as a platform to present products from each vendor and the home page will be used to capture an overview and draw users deeper into the site. You can view our current site - which needs A LOT of help to get ideas on products represented and types of products

Target Market(s)

Engineers and Pharmaceutical / Bio pharm end users

Industry/Entity Type

E-Commerce

Number of Pages Required

2 page

Font styles to use
Sans Serif

Requirements
Must have
• I need a home page that provides a snapshot of my company and the product lines we represent - then a second page that I can copy as a template for each line I rep as well as for an "About us / contact" page.
• I would like to be able to manage content on the pages so something easy to adjust pictures or add content is a must
• Must use our logo

```html
<!DOCTYPE html>
<html lang="en">
<head>
<meta charset="utf-8">
<title>Central Bio</title>
<link href="https://fonts.googleapis.com/css2?family=Montserrat:wght@600;700&family=Roboto:wght@400;500;700&family=Arimo:wght@400;700&display=swap" rel="stylesheet">
<style>
:root{
  --orange:#f15a24;
  --navy:#1f1a5e;
  --ink:#333;
  --muted:#555;
  --grey-band:#e2e2e2;
  --card:#f3f3f3;
  --line:#d6d6d6;
  --white:#fff;
}
*{margin:0;padding:0;box-sizing:border-box}
html,body{width:732px;height:1200px;overflow:hidden;background:var(--white)}
body{position:relative;font-family:"Arimo",Arial,sans-serif;color:var(--ink)}
.abs{position:absolute}

/* header */
.topbar{left:0;top:0;width:732px;height:34px;background:var(--orange)}
.hero-photo{left:0;top:0;width:732px;height:380px;
  background:
   radial-gradient(ellipse at 78% 30%,#e9e4e1 0,#f2f2f4 30%,rgba(255,255,255,0) 60%),
   radial-gradient(ellipse at 62% 78%,#2a4fd0 0,#5a7be6 18%,rgba(255,255,255,0) 42%),
   linear-gradient(90deg,#fbfcfd 0,#f4f7fa 40%,#e8eef4 100%)}
.hero-fade{left:0;top:330px;width:732px;height:50px;background:linear-gradient(rgba(255,255,255,0),#fff)}
.brand-box{left:61px;top:0;width:241px;height:70px;background:var(--white);box-shadow:0 2px 5px rgba(0,0,0,.18);display:flex;align-items:center;padding-left:22px;gap:8px}
.brand-dot{width:22px;height:22px;border-radius:50%;background:var(--orange)}
.brand-name{font-family:"Montserrat",sans-serif;font-weight:600;font-size:23px;color:var(--navy);letter-spacing:-.3px}
.nav-link{top:12px;color:var(--white);text-decoration:none;font-family:"Arimo",sans-serif;font-size:9.5px;line-height:11px}
.hero-title{left:72px;top:178px;font-family:"Montserrat",sans-serif;font-weight:700;font-size:47px;color:var(--orange);letter-spacing:.5px}
.hero-sub{left:74px;top:230px;font-family:"Montserrat",sans-serif;font-weight:600;font-size:21px;color:var(--navy)}
.hero-text{left:76px;top:263px;width:222px;font-size:8.8px;line-height:12.2px;color:#444}

/* main panel */
.panel{left:61px;top:365px;width:609px;height:776px;background:var(--white);box-shadow:0 0 3px rgba(0,0,0,.25)}
.section-title{font-family:"Roboto",sans-serif;font-weight:500;font-size:13.5px;color:var(--navy);display:flex;align-items:center}
.section-title b{font-weight:500;margin-right:4px;color:#222}
.section-title .rule-dot{width:8px;height:8px;border-radius:50%;background:var(--line);margin-left:16px}
.rule{height:1px;background:var(--line)}
.about-text{left:82px;top:416px;width:550px;text-align:center;font-size:9.1px;line-height:12.2px;color:var(--muted)}

.card{top:562px;width:141px;height:194px;background:var(--card)}
.card-head{height:22px;background:var(--grey-band);font-family:"Roboto",sans-serif;font-size:10px;color:#444;text-align:center;line-height:24px;letter-spacing:.3px}
.card-img{margin:13px auto 0;width:129px;height:77px}
.card-text{margin:7px 6px 0;font-size:7.6px;line-height:9.6px;color:#444;text-align:justify}
.card-btn{position:absolute;left:4px;right:4px;bottom:13px;height:17px;background:var(--orange);color:var(--white);font-size:8.6px;text-align:center;line-height:17px}

.product{left:66px;width:390px;height:40px}
.product-name{position:absolute;left:0;top:0;width:118px;height:40px;display:flex;align-items:center;font-family:"Arimo",sans-serif;font-weight:700;font-size:13px;color:#1a56b8}
.product-desc{position:absolute;left:128px;top:0;width:264px;font-size:7.4px;line-height:11px;color:#444}
.product-desc strong{display:block;color:#222}

.enquiry{left:472px;top:794px;width:189px;height:328px;background:#f1f1f1}
.enq-title{left:492px;top:803px;font-family:"Montserrat",sans-serif;font-weight:600;font-size:13px;letter-spacing:1px;color:var(--navy)}
.enq-rule{left:492px;top:826px;width:157px;height:1px;background:var(--line)}
.enq-text{left:492px;top:834px;width:156px;font-size:7.4px;line-height:10.6px;color:#333}
.field{left:490px;width:152px;height:22px;border:1px solid #d4d4d4;border-radius:11px;background:var(--white);font-size:7.4px;color:#444;padding:6px 0 0 12px}
.field-area{left:493px;top:992px;width:149px;height:79px;border-radius:10px;padding-top:10px}
.submit{left:575px;top:1087px;width:66px;height:20px;background:var(--navy);border-radius:7px;color:var(--white);font-size:7.8px;text-align:center;line-height:20px}

/* footer */
.footer{left:0;top:1138px;width:732px;height:62px;background:var(--navy);border-top:3px solid var(--orange)}
.foot-links{left:66px;top:1154px;color:var(--white);font-size:9.6px;display:flex;gap:16px}
.foot-copy{left:66px;top:1171px;color:var(--white);font-size:9px}
.foot-brand{left:504px;top:1152px;display:flex;align-items:center;gap:7px}
.foot-brand .brand-dot{width:18px;height:18px}
.foot-brand .brand-name{color:var(--white);font-size:20px}
</style>
</head>
<body>

<div class="abs hero-photo" role="img" aria-label="Scientist in lab coat and blue gloves writing on a sample plate in a laboratory"></div>
<div class="abs hero-fade"></div>
<div class="abs topbar"></div>
<nav>
  <a class="abs nav-link" href="#" style="left:333px">Home</a>
  <a class="abs nav-link" href="#" style="left:378px">About</a>
  <a class="abs nav-link" href="#" style="left:424px">Solutions</a>
  <a class="abs nav-link" href="#" style="left:483px">Features</a>
  <a class="abs nav-link" href="#" style="left:542px">Customers</a>
  <a class="abs nav-link" href="#" style="left:608px">Schedule demo</a>
</nav>
<div class="abs brand-box"><span class="brand-dot"></span><span class="brand-name">Central Bio</span></div>

<h1 class="abs hero-title">SPECIALIST</h1>
<h2 class="abs hero-sub">LOREM IPSUM DOLOR</h2>
<p class="abs hero-text">Labplanner has almost entirely eliminated the time needed to manage the scheduling anfd fees and our students and industrial partners really like how easy it is use. The customer service we have received form Workbench has been oustanding.</p>

<div class="abs panel"></div>

<div class="abs section-title" style="left:78px;top:387px"><b>What</b>Central Bio Do<span class="rule-dot"></span></div>
<div class="abs rule" style="left:236px;top:394px;width:426px"></div>
<p class="abs about-text">Lorem Ipsum is simply dummy text of the printing and typesetting industry. Lorem Ipsum has been the industry's standard dummy text ever since the 1500s, when an unknown printer took a galley of type and scrambled it to make a type specimen book. It has survived not only five centuries, but also the leap into electronic typesetting, remaining essentially unchanged. It was popularised in the 1960s with the release of Typeline sheets containing Lorem Ipsum passages, and more recently with desktop publishing software like LayoutPro including versions of Lorem Ipsum.</p>

<div class="abs section-title" style="left:78px;top:527px"><b>What</b>Central Bio Offer<span class="rule-dot"></span></div>
<div class="abs rule" style="left:246px;top:534px;width:416px"></div>

<div class="abs card" style="left:70px">
  <div class="card-head">LOREM IPSUM</div>
  <div class="card-img" role="img" aria-label="Silicone tubing and single-use fittings" style="background:radial-gradient(circle at 60% 45%,#9fb3c9,#3b5779 55%,#1d2a45)"></div>
  <p class="card-text">Lorem Ipsum is simply dummy text of the pring and typesetting industry. Lorem Ipsum has been the industry's standard.</p>
  <div class="card-btn">Readmore</div>
</div>
<div class="abs card" style="left:220px">
  <div class="card-head">LOREM IPSUM</div>
  <div class="card-img" role="img" aria-label="Peristaltic pump unit" style="background:linear-gradient(160deg,#d9e6f2,#6d8fbf 55%,#3c5f9a)"></div>
  <p class="card-text">Lorem Ipsum is simply dummy text of the pring and typesetting industry. Lorem Ipsum has been the industry's standard.</p>
  <div class="card-btn">Readmore</div>
</div>
<div class="abs card" style="left:370px">
  <div class="card-head">LOREM IPSUM</div>
  <div class="card-img" role="img" aria-label="Red liquid filling pump with display" style="background:linear-gradient(120deg,#c91e24,#e8463f 55%,#f0e6d6)"></div>
  <p class="card-text">Lorem Ipsum is simply dummy text of the pring and typesetting industry. Lorem Ipsum has been the industry's standard.</p>
  <div class="card-btn">Readmore</div>
</div>
<div class="abs card" style="left:519px">
  <div class="card-head">LOREM IPSUM</div>
  <div class="card-img" role="img" aria-label="Stainless bioprocess equipment in a clean room" style="background:linear-gradient(180deg,#f4f6f8,#c8d0d8 60%,#8d98a3)"></div>
  <p class="card-text">Lorem Ipsum is simply dummy text of the pring and typesetting industry. Lorem Ipsum has been the industry's standard.</p>
  <div class="card-btn">Readmore</div>
</div>

<div class="abs section-title" style="left:73px;top:787px;color:var(--navy)">Our Products<span class="rule-dot"></span></div>
<div class="abs rule" style="left:170px;top:794px;width:278px"></div>

<div class="abs product" style="top:840px">
  <div class="product-name">Flexline Hose Co.</div>
  <p class="product-desc"><strong>Specialist manufacturers of PTFE lined flexible hoses</strong>Concept, design and production of single use assemblies, custom carboys, tubing manifolds and other products designed for cGMP applications</p>
</div>
<div class="abs product" style="top:893px">
  <div class="product-name" style="color:#2a7fc0">PureSeal</div>
  <p class="product-desc"><strong>PureSeal, Inc. provides cGMP manufactured components.</strong>Concept, design and production of single use assemblies, custom carboys, tubing manifolds and other products designed for cGMP applications</p>
</div>
<div class="abs product" style="top:951px">
  <div class="product-name" style="font-size:18px">Fluxon</div>
  <p class="product-desc"><strong>Fluxon peristaltic liquid filling pumps, controls and systems</strong>Concept, design and production of single use assemblies, custom carboys, tubing manifolds and other products designed for cGMP applications</p>
</div>
<div class="abs product" style="top:1011px">
  <div class="product-name" style="font-size:19px;color:#2b3a16">Finera</div>
  <p class="product-desc"><strong>Finera Solutions offers an for bio-process management</strong>Concept, design and production of single use assemblies, custom carboys, tubing manifolds and other products designed for cGMP applications</p>
</div>
<div class="abs product" style="top:1075px">
  <div class="product-name" style="color:#555">Stellar Polymers</div>
  <p class="product-desc"><strong>Stellar Polymers pioneers in silicone</strong>Concept, design and production of single use assemblies, custom carboys, tubing manifolds and other products designed for cGMP applications</p>
</div>

<div class="abs enquiry"></div>
<div class="abs enq-title">QUICK ENQUIRY</div>
<div class="abs enq-rule"></div>
<p class="abs enq-text">In hac habitasse platea dictumst. Donec commodo, purus sit amet luctus placerat, nunc nulla congue enim, vitae vulputate mauris ligula nec orci.</p>
<div class="abs field" style="top:896px">Your Name</div>
<div class="abs field" style="top:927px">Your Email</div>
<div class="abs field" style="top:958px">Your Phone</div>
<div class="abs field field-area">Additional Information</div>
<div class="abs submit">Submit Form</div>

<footer class="abs footer"></footer>
<div class="abs foot-links"><span>Home</span><span>|</span><span>Contact Us</span><span>|</span><span>Products</span></div>
<div class="abs foot-copy">© Central Biosolutions, Corp.</div>
<div class="abs foot-brand"><span class="brand-dot"></span><span class="brand-name">Central Bio</span></div>

</body>
</html>
```